Velvet Lantern rebranding my business with a new business card

I have my new logo and now I need a refresher on my business cards. I really want something fun and fresh. I like black background or anything to make the color pop.
Logo
Name: Velvet Lantern
Contact Info as stated below:
Mira Pellow
555-013-4762
Logo
Name: Velvet Lantern
Mira Pellow
555-013-4762
fb.me/VelvetLanternbyMira
Instagram: @VelvetLanternbyMira

Industry/Entity Type

Business

Contact Information for Business Card

double-sided. Logo on one side. Contact info on the other.

Requirements
Must have
• Logo
• Name: Velvet Lantern
• Contact Info as stated below:
• Mira Pellow
• 555-013-4762
• fb.me/VelvetLanternbyMira
• fb.me/VelvetLanternbyMira

```html
<!DOCTYPE html>
<html lang="en">
<head>
<meta charset="utf-8">
<title>Velvet Lantern – Business Card</title>
<link rel="stylesheet" href="https://fonts.googleapis.com/css2?family=Oswald:wght@500&family=Roboto:wght@300;400&display=swap">
<style>
  :root {
    --backdrop: #2b2b2d;
    --card: #1f1f20;
    --card-edge: #2a2a2b;
    --pink: #f4b9c8;
    --pink-soft: #f7d3dc;
    --white: #f2f2f2;
    --rule: #8a8a8a;
    --badge: #ffffff;
  }
  * { box-sizing: border-box; margin: 0; padding: 0; }
  html, body {
    width: 1200px;
    height: 900px;
    overflow: hidden;
    background: var(--backdrop);
  }
  .stage {
    position: relative;
    width: 1200px;
    height: 900px;
  }
  .card {
    position: absolute;
    left: 290px;
    width: 620px;
    height: 354px;
    background: var(--card);
    border: 1px solid var(--card-edge);
    box-shadow: 0 10px 30px rgba(0,0,0,0.35);
  }
  .card--front { top: 76px; }
  .card--back { top: 470px; }

  /* Front */
  .logo-badge {
    position: absolute;
    left: 50%;
    top: 44px;
    width: 176px;
    height: 176px;
    margin-left: -88px;
    border-radius: 50%;
    background: var(--badge);
    box-shadow: inset 0 0 0 6px var(--badge), inset 0 0 0 8px var(--pink-soft), inset 0 0 0 11px var(--badge), inset 0 0 0 12px var(--pink);
    display: flex;
    align-items: center;
    justify-content: center;
    text-align: center;
  }
  .logo-name {
    font-family: "Roboto", sans-serif;
    font-weight: 400;
    font-size: 22px;
    line-height: 1.15;
    color: var(--pink);
    letter-spacing: 1px;
  }
  .site-url {
    position: absolute;
    left: 0;
    right: 0;
    top: 262px;
    text-align: center;
    font-family: "Roboto", sans-serif;
    font-weight: 300;
    font-size: 15px;
    letter-spacing: 6px;
    color: var(--white);
  }

  /* Back */
  .holder-name {
    position: absolute;
    right: 340px;
    top: 146px;
    font-family: "Oswald", sans-serif;
    font-weight: 500;
    font-size: 34px;
    letter-spacing: 0.5px;
    color: var(--pink);
    text-transform: uppercase;
    white-space: nowrap;
  }
  .divider {
    position: absolute;
    left: 296px;
    top: 118px;
    width: 1px;
    height: 110px;
    background: var(--rule);
  }
  .contact-list {
    position: absolute;
    left: 318px;
    top: 134px;
    list-style: none;
    font-family: "Roboto", sans-serif;
    font-weight: 400;
    font-size: 17px;
    color: var(--white);
  }
  .contact-item {
    display: flex;
    align-items: center;
    height: 27px;
  }
  .contact-icon {
    width: 14px;
    height: 14px;
    margin-right: 12px;
    flex: none;
  }
</style>
</head>
<body>
<main class="stage">
  <section class="card card--front" aria-label="Card front">
    <div class="logo-badge">
      <span class="logo-name">Velvet<br>Lantern</span>
    </div>
    <p class="site-url">www.velvetlantern.com</p>
  </section>

  <section class="card card--back" aria-label="Card back">
    <h1 class="holder-name">Mira Pellow</h1>
    <div class="divider"></div>
    <ul class="contact-list">
      <li class="contact-item">
        <svg class="contact-icon" viewBox="0 0 24 24" aria-hidden="true">
          <path fill="#f2f2f2" d="M6.6 10.8a15.1 15.1 0 0 0 6.6 6.6l2.2-2.2c.3-.3.7-.4 1-.2 1.1.4 2.3.6 3.6.6.6 0 1 .4 1 1V20c0 .6-.4 1-1 1A17 17 0 0 1 3 4c0-.6.4-1 1-1h3.5c.6 0 1 .4 1 1 0 1.3.2 2.5.6 3.6.1.3 0 .7-.2 1z"/>
        </svg>
        555-013-4762
      </li>
      <li class="contact-item">
        <svg class="contact-icon" viewBox="0 0 24 24" aria-hidden="true">
          <circle cx="12" cy="12" r="10" fill="#f2f2f2"/>
        </svg>
        www.velvetlantern.com
      </li>
      <li class="contact-item">
        <svg class="contact-icon" viewBox="0 0 24 24" aria-hidden="true">
          <rect x="2" y="2" width="20" height="20" fill="#f2f2f2"/>
        </svg>
        fb.me/VelvetLanternbyMira
      </li>
    </ul>
  </section>
</main>
</body>
</html>
```